www.marvenholt.com

Updating website so looks futristic but yet business like and easy to navigate, essentially a good landing page with a cool picture summing up what we do, and links to the following pages, all other pages on site to be updated, Exclusive Distributor of Brisk Forge Unique Fitness Equipment Products in UK & Ireland, www.crestvolley.co.uk Exclusive Partners & Distributors Of Crest Volley - Obstacle Races - Obstacle Hire - Obstacle Training - Adventure Events, www.goplumwick.co.uk Adventures That Inspire. We also Health Club / Facillity Consultancy

```html
<!DOCTYPE html>
<html lang="en">
<head>
<meta charset="utf-8">
<title>Marven Holt — Commercial Fitness, OCR / Events, Consultancy</title>
<link href="https://fonts.googleapis.com/css2?family=Roboto+Condensed:wght@400;500;700&display=swap" rel="stylesheet">
<style>
  :root {
    --orange: #ff6b0a;
    --bar: #1b1b1b;
    --ink: #0a0a0a;
    --light: #e4e4e4;
    --white: #ffffff;
  }
  * { margin: 0; padding: 0; box-sizing: border-box; }
  html, body { width: 1093px; height: 1200px; overflow: hidden; background: var(--ink); }
  body { position: relative; font-family: 'Roboto Condensed', 'Arial Narrow', sans-serif; color: var(--white); }

  .site-nav {
    position: absolute; left: 0; top: 0; width: 1093px; height: 76px;
    background: var(--bar);
    display: flex; align-items: center; padding-left: 159px;
  }
  .site-nav::after {
    content: ""; position: absolute; left: 0; bottom: 0; width: 100%; height: 2px;
    background: linear-gradient(90deg, rgba(255,107,10,0.2), var(--orange) 40%, rgba(255,107,10,0) 85%);
  }
  .nav-item {
    font-size: 21px; font-weight: 500; letter-spacing: 0.2px; color: var(--white);
    text-transform: uppercase; text-decoration: none; padding: 0 21px; line-height: 28px;
    border-left: 2px solid var(--white);
  }
  .nav-item:first-child { border-left: none; padding-left: 0; }
  .nav-item.is-active { color: var(--orange); }
  .nav-search { position: absolute; left: 1028px; top: 27px; }

  .hero {
    position: absolute; left: 0; top: 76px; width: 1093px; height: 509px;
    background: #000;
  }
  .hero-photo {
    position: absolute; inset: 0;
    background:
      linear-gradient(90deg, rgba(0,0,0,0) 0%, rgba(0,0,0,0) 42%, rgba(0,0,0,0.85) 62%, #000 75%),
      radial-gradient(ellipse at 30% 40%, #6c7078 0%, #3f444c 40%, #24272c 75%, #15171a 100%);
  }
  .hero::after {
    content: ""; position: absolute; left: 0; bottom: 0; width: 100%; height: 2px;
    background: linear-gradient(90deg, rgba(255,107,10,0.3), var(--orange) 40%, rgba(255,107,10,0) 85%);
  }
  .hero-title {
    position: absolute; right: 61px; top: 154px;
    font-size: 66px; font-weight: 700; line-height: 1; letter-spacing: 0.5px; color: var(--light);
  }
  .hero-title .accent { color: var(--orange); }
  .hero-title .rest { font-weight: 500; }
  .hero-tagline {
    position: absolute; right: 61px; top: 233px;
    font-size: 21px; font-weight: 500; color: var(--light); letter-spacing: 0.1px;
  }
  .hero-cta {
    position: absolute; left: 772px; top: 290px; width: 245px; height: 80px;
    background: var(--orange); color: var(--light);
    font-size: 37px; font-weight: 500; text-decoration: none;
    display: flex; align-items: center; justify-content: center;
  }

  .experts { position: absolute; left: 0; top: 585px; width: 1093px; height: 615px; background: #080808; }
  .experts-photo {
    position: absolute; left: 437px; top: 66px; width: 656px; height: 442px;
    background:
      radial-gradient(ellipse at 55% 50%, rgba(0,0,0,0) 35%, rgba(8,8,8,0.9) 75%, #080808 95%),
      linear-gradient(180deg, #8d8f92 0%, #6b6a6b 40%, #4a3b3a 70%, #2a2524 100%);
  }
  .experts-heading {
    position: absolute; left: 57px; top: 122px;
    font-size: 31px; font-weight: 700; color: var(--orange); letter-spacing: 0.2px;
  }
  .experts-body {
    position: absolute; left: 57px; top: 171px; width: 380px;
    font-size: 14px; line-height: 20.9px; color: var(--white); text-align: justify; hyphens: auto;
  }
  .footer-band { position: absolute; left: 0; top: 1175px; width: 1093px; height: 25px; background: #141414; }
</style>
</head>
<body>
  <nav class="site-nav">
    <a class="nav-item is-active" href="#">Home</a>
    <a class="nav-item" href="#">About Us</a>
    <a class="nav-item" href="#">Our Team</a>
    <a class="nav-item" href="#">Testimonial</a>
    <a class="nav-item" href="#">Health</a>
    <a class="nav-item" href="#">Wellness</a>
    <a class="nav-item" href="#">Fitness</a>
    <svg class="nav-search" width="28" height="28" viewBox="0 0 28 28" aria-label="Search">
      <circle cx="11" cy="11" r="8.5" fill="none" stroke="#b9b9b9" stroke-width="2.5"/>
      <line x1="17.5" y1="17.5" x2="25" y2="25" stroke="#b9b9b9" stroke-width="3" stroke-linecap="round"/>
    </svg>
  </nav>

  <header class="hero">
    <div class="hero-photo" role="img" aria-label="Athlete doing a renegade row with dumbbells in a dim gym"></div>
    <h1 class="hero-title"><span class="accent">MARVEN</span> <span class="rest">HOLT</span></h1>
    <p class="hero-tagline">COMMERCIAL FITNESS, OCR / EVENTS, CONSULTANCY.</p>
    <a class="hero-cta" href="#">CONSULT NOW!</a>
  </header>

  <section class="experts">
    <div class="experts-photo" role="img" aria-label="Group training on bodyweight resistance machines on a rooftop"></div>
    <h2 class="experts-heading">EXPERTS IN THE INDUSTRY</h2>
    <p class="experts-body">Marven Holt are leading consultants to the Health, Wellness and Fitness industry, with over 25 years experience working with some of the biggest global worldwide brands from equipment providers and facility operators to mass participation events and obstacle course races. Marven Holt is a multi disciplined business specialising in helping brands grow through insight, strategy creation and valuable sector collaboration, recent clients include the exclusive distribution of Brisk Forge bodyweight training products for the UK and Ireland, exclusive distribution of fitness app Pulsegrid, Ironridge Trail Race, Crest Volley, Vantora Fitness, Kelvane UK, Brightmoor Leisure, Active Dunholme, Ashcombe Community Leisure, Slimpath Coach, VitaMove and the regional health trust. The Marven Holt team specialise in a bespoke, consultative approach for each project and pride ourselves in our attention to detail with passion and dedication</p>
    <div class="footer-band"></div>
  </section>
</body>
</html>
```